Wordpress template for a mens-choire webpage

Task is to design a Wordpress template for an 98 years old estonian mens choire webpage.
Design should involve details from the attached files, choire logo and the colors of the choire flag: in horizontal orientation bright sky-blue, white, bright grass-green.
Designer signature is allowed to be added to the template, with country of origin.

Reason: Deadline extended 2 days (until 2. March 2014) to accommodate designers creativity.

Thank you everyone for your great designs!
Our project has now entered into a voting and decision phase until 14th of March 2014 (included).

```html
<!DOCTYPE html>
<html lang="en">
<head>
<meta charset="utf-8">
<title>Ilo Meeskoor</title>
<link rel="stylesheet" href="https://fonts.googleapis.com/css2?family=Open+Sans:wght@400;600&family=Roboto:wght@400&display=swap">
<style>
:root{
  --green:#5a9e24;
  --blue:#1e6db3;
  --sky:#1aa0e8;
  --nav:#16a3ea;
  --nav-active:#0a6fd1;
  --ink:#333;
  --muted:#555;
  --red:#e0161b;
  --panel:#dcdcdc;
  --footer:#282828;
  --page:#f7f7f7;
}
*{box-sizing:border-box;margin:0;padding:0}
a{text-decoration:none}
html,body{width:1200px;height:1161px;overflow:hidden}
body{position:relative;background:#fff;font-family:"Open Sans",Arial,sans-serif;color:var(--ink)}
.backdrop{position:absolute;left:0;top:0}
.page{position:absolute;left:140px;top:0;width:920px;height:1059px;background:var(--page)}
.abs{position:absolute}
.brand{left:171px;top:0;width:80px;height:100px;background:#fff;display:flex;flex-direction:column;align-items:center;justify-content:center;gap:6px}
.brand .dot{width:34px;height:34px;border-radius:50%;background:#b0171d}
.brand span{font-size:10px;font-weight:600;color:#b0171d;text-align:center;line-height:1.15}
.login{left:651px;top:17px;font-size:13px;color:#444}
.phone{left:714px;top:13px;font-size:17px;color:var(--blue);display:flex;align-items:center;gap:3px}
.social-top{left:866px;top:13px;display:flex;gap:4px}
.social-top i{width:24px;height:24px;border-radius:50%;background:#2b2b2b;display:block}
.nav{left:584px;top:57px;width:445px;height:33px;background:var(--nav);display:flex}
.nav a{color:#fff;font-size:16px;line-height:33px;padding:0 9px}
.nav a.active{background:var(--nav-active)}
.slider{left:171px;top:100px;width:858px;height:451px;background:radial-gradient(ellipse at 50% 45%,#4a3a3a 0%,#2a2020 45%,#0b0b0b 100%)}
.caption{left:171px;top:500px;width:858px;height:51px;background:#000;color:#fff}
.caption h2{position:absolute;left:27px;top:12px;font-size:21px;font-weight:400}
.dots{position:absolute;right:24px;top:21px;display:flex;gap:9px}
.dots i{width:14px;height:14px;background:#fff;display:block}
.dots i.on{background:#2f8fe0}
.panel-head{height:43px;background:var(--panel);font-size:19px;padding:13px 10px 0;color:#222}
.about{left:171px;top:566px;width:288px}
.about .photo{height:115px;margin-top:2px;background:linear-gradient(180deg,#8fb0d3 0%,#c3d3e0 45%,#2c3440 70%,#1c2128 100%)}
.about p{font-size:10.4px;line-height:15.5px;color:var(--muted);text-align:justify;text-align-last:justify;margin-top:10px;height:47px;overflow:hidden}
.btn{display:inline-block;background:linear-gradient(#2a8be8,#0b5fc4);color:#fff;border-radius:2px}
.about .btn{position:absolute;left:187px;top:228px;width:101px;height:23px;font-size:13px;line-height:23px;text-align:center}
.events{left:474px;top:566px;width:555px}
.arrows{position:absolute;right:11px;top:9px;display:flex;gap:2px}
.arrows span{width:27px;height:27px;background:#000;display:flex;align-items:center;justify-content:center}
.card{position:absolute;width:270px;height:102px;background:linear-gradient(#fff,#e4e4e4);border:1px solid #cfcfcf}
.card .thumb{position:absolute;left:13px;top:12px;width:108px;height:78px;background:linear-gradient(135deg,#3a2a2a,#0e0e0e)}
.card .date{position:absolute;left:133px;top:13px;font-size:13px;color:var(--red)}
.card p{position:absolute;left:133px;top:32px;font-size:12.4px;line-height:16px;color:#444;width:130px}
.card .btn{position:absolute;left:133px;top:70px;width:68px;height:15px;font-size:8px;line-height:15px;text-align:center}
.blog-title,.video-title{font-size:15px;font-weight:600;color:#222}
.blog-title{left:171px;top:842px}
.video-title{left:694px;top:842px;font-size:14px}
.blog-arrows{left:618px;top:843px;display:flex;gap:1px}
.blog-arrows span{width:14px;height:14px;background:#555;display:flex;align-items:center;justify-content:center}
.post{left:171px;width:478px;height:80px;background:#fff;border:1px solid #d8d8d8}
.post .thumb{position:absolute;left:3px;top:4px;width:88px;height:70px;background:linear-gradient(135deg,#6a2020,#191919 60%,#d0c8b8)}
.post h3{position:absolute;left:103px;top:5px;font-size:12.5px;font-weight:400;color:var(--red);font-family:Arial,sans-serif}
.post p{position:absolute;left:103px;top:21px;font-size:10.4px;line-height:14px;color:#555;font-family:Arial,sans-serif;width:370px}
.share{position:absolute;left:103px;top:53px;display:flex;gap:36px}
.share div{display:flex;gap:3px}
.share b{font-size:9px;font-weight:600;border:1px solid #ccc;background:#f4f4f4;padding:1px 4px;color:#333}
.share em{font-style:normal;font-size:9px;border:1px solid #ccc;background:#fff;padding:1px 4px}
.video{left:698px;top:866px;width:327px;height:174px;background:radial-gradient(ellipse at 50% 40%,#9a9a9a,#4a4a4a 70%,#2e2e2e)}
.play{position:absolute;left:126px;top:33px}
.video .bar{position:absolute;left:0;bottom:13px;width:100%;height:4px;background:#d81818}
.video .ctrl{position:absolute;left:0;bottom:0;width:100%;height:13px;background:#111;font-size:7px;color:#aaa;padding:2px 60px}
.footer{left:0;top:1059px;width:1200px;height:102px;background:var(--footer)}
.copy{left:174px;top:1103px;font-family:Roboto,Arial,sans-serif;font-size:12px;color:#eee}
.social-foot{left:827px;top:1095px;display:flex;gap:10px}
.social-foot i{width:32px;height:32px;border-radius:50%;display:block;border:2px solid #444}
</style>
</head>
<body>
<svg class="backdrop" width="1200" height="1059" viewBox="0 0 1200 1059" aria-hidden="true">
  <path d="M0 0H140V400Q70 410 0 428Z" fill="var(--green)"/>
  <path d="M1060 0H1200V150Q1130 240 1060 283Z" fill="var(--green)"/>
  <path d="M140 725Q40 780 0 890V1059H140Z" fill="var(--blue)"/>
  <path d="M1060 587Q1130 560 1200 546V1059H1060Z" fill="var(--blue)"/>
</svg>
<div class="page"></div>

<header>
  <div class="abs brand"><i class="dot"></i><span>Ilo<br>Meeskoor</span></div>
  <div class="abs login">LOG IN</div>
  <div class="abs phone">
    <svg width="11" height="14" viewBox="0 0 11 14"><path d="M3 1L1 2Q0 7 5 12L7 13L9 10L7 8L5 9Q3 7 3 5L5 4Z" fill="var(--muted)"/></svg>
    1-800-555-0199
  </div>
  <div class="abs social-top"><i></i><i></i><i></i><i></i><i></i><i></i></div>
  <nav class="abs nav">
    <a class="active" href="#">HOME</a><a href="#">ABOUT US</a><a href="#">SERVICE</a><a href="#">EVENTS</a><a href="#">CONTACTS</a>
  </nav>
</header>

<section>
  <div class="abs slider" role="img" aria-label="Group photo of the choir in dark suits on a stage"></div>
  <div class="abs caption">
    <h2>98 YEARS OF ESTONIAN CHOIRE</h2>
    <div class="dots"><i class="on"></i><i></i><i></i><i></i></div>
  </div>
</section>

<section class="abs about">
  <div class="panel-head">ABOUT US</div>
  <div class="photo" role="img" aria-label="Choir singers in tuxedos standing in a line by the sea"></div>
  <p>ilo meeskoor is a Professor of Practice at the Harlow School where he teaches Innovation and Product Development in Harlow’s undergraduate, MBA, and</p>
  <a class="btn" href="#">READ MORE</a>
</section>

<section class="abs events">
  <div class="panel-head">UPCOMING EVENT</div>
  <div class="arrows">
    <span><svg width="10" height="16"><path d="M8 1L2 8L8 15" stroke="#fff" stroke-width="1.6" fill="none"/></svg></span>
    <span><svg width="10" height="16"><path d="M2 1L8 8L2 15" stroke="#fff" stroke-width="1.6" fill="none"/></svg></span>
  </div>
  <div class="card" style="left:0;top:45px"><div class="thumb" role="img" aria-label="Choir seated in a concert hall"></div><div class="date">Feb.25, 2014</div><p>Praesent vestibulum aenean nonummy</p><a class="btn" href="#">READ MORE</a></div>
  <div class="card" style="left:285px;top:45px"><div class="thumb" role="img" aria-label="Singers performing close up"></div><div class="date">Feb.15, 2014</div><p>Praesent vestibulum aenean nonummy</p><a class="btn" href="#">READ MORE</a></div>
  <div class="card" style="left:0;top:150px"><div class="thumb" role="img" aria-label="Choir on a dark stage"></div><div class="date">Feb.12, 2014</div><p>Praesent vestibulum aenean nonummy</p><a class="btn" href="#">READ MORE</a></div>
  <div class="card" style="left:285px;top:150px"><div class="thumb" role="img" aria-label="Choir members posing in tuxedos"></div><div class="date">Feb.19, 2014</div><p>Praesent vestibulum aenean nonummy</p><a class="btn" href="#">READ MORE</a></div>
</section>

<section>
  <h2 class="abs blog-title">BLOG</h2>
  <div class="abs blog-arrows">
    <span><svg width="6" height="10"><path d="M5 1L1 5L5 9" stroke="#fff" fill="none"/></svg></span>
    <span><svg width="6" height="10"><path d="M1 1L5 5L1 9" stroke="#fff" fill="none"/></svg></span>
  </div>
  <article class="abs post" style="top:866px">
    <div class="thumb" role="img" aria-label="Singers in concert uniforms"></div>
    <h3>The Angriest BRIX Minifigs</h3>
    <p>BRIX friends is the latest attempt by BRIX to attract young girls to the brand. Market Weekly covered the launch extensively and well in a cover story</p>
    <div class="share"><div><b>+1</b><em>0</em></div><div><b>Post</b><em>0</em></div><div><b>Share</b></div></div>
  </article>
  <article class="abs post" style="top:958px">
    <div class="thumb" role="img" aria-label="Choir rows in concert uniforms"></div>
    <h3>The Angriest BRIX Minifigs</h3>
    <p>BRIX friends is the latest attempt by BRIX to attract young girls to the brand. Market Weekly covered the launch extensively and well in a cover story</p>
    <div class="share"><div><b>+1</b><em>0</em></div><div><b>Post</b><em>0</em></div><div><b>Share</b></div></div>
  </article>
</section>

<section>
  <h2 class="abs video-title">VIDEOS</h2>
  <div class="abs video" role="img" aria-label="Video of the choir standing on stone steps">
    <svg class="play" width="76" height="76" viewBox="0 0 76 76"><circle cx="38" cy="38" r="34" fill="none" stroke="#fff" stroke-width="5" opacity=".85"/><path d="M30 22L54 38L30 54Z" fill="#fff" opacity=".85"/></svg>
    <div class="bar"></div>
    <div class="ctrl">0:00</div>
  </div>
</section>

<footer class="abs footer"></footer>
<div class="abs copy">© 2014 Ilo Meeskoor All Rights Reserved</div>
<div class="abs social-foot">
  <i style="background:#29a9e1"></i><i style="background:#3b5ba8"></i><i style="background:#6a6a6a"></i><i style="background:#e5508f"></i><i style="background:#fafafa"></i>
</div>
</body>
</html>
```